SkyvornQ Business Cards and Stationary Design

Need a design for our business cards and stationary. I want to carry on the theme of the logo. I want the business cards to have a design on the back. I would like the business cards and the stationary to carry the same theme, design scheme, and branding

Target Market(s)

Airlines and Maintenance Facilities

Industry/Entity Type

Aviation

Contact Information for Business Card

Name
Position Title
Address: 4827 Trellis Hollow Road, Fort Pierce, Florida, 34951
Office Number
Mobile Number
Email
Website

Font styles to use
Serif
Sans Serif

Colors

Designer to choose colors to be used in the design.

```html
<!DOCTYPE html>
<html lang="en">
<head>
<meta charset="utf-8">
<title>SkyvornQ Business Card</title>
<link href="https://fonts.googleapis.com/css2?family=Exo+2:wght@400;600;700&display=swap" rel="stylesheet">
<style>
  :root {
    --backdrop: #8a8a8a;
    --paper: #ededed;
    --navy: #10295a;
    --ink: #2b2f38;
    --rule: #a9a9a9;
    --blue-light: #0a9fe3;
    --blue-mid: #0877c9;
    --blue-deep: #0a4f9a;
    --white: #ffffff;
  }
  html, body {
    margin: 0;
    width: 1200px;
    height: 1200px;
    overflow: hidden;
    background: var(--backdrop);
    font-family: "Exo 2", sans-serif;
  }
  .canvas { position: relative; width: 1200px; height: 1200px; }
  .card {
    position: absolute;
    top: 310px;
    height: 594px;
    box-shadow: 0 3px 6px rgba(0,0,0,0.35);
  }
  .card-front { left: 234px; width: 364px; background: var(--paper); color: var(--ink); text-align: center; }
  .card-back {
    left: 627px; width: 370px;
    background: radial-gradient(circle at 50% 48%, var(--blue-light) 0%, var(--blue-mid) 45%, var(--blue-deep) 100%);
    color: var(--white); text-align: center;
  }
  .brand-ring { position: absolute; left: 50%; transform: translateX(-50%); }
  .front-ring { top: 102px; }
  .back-ring { top: 223px; }
  .brand-name {
    position: absolute; left: 0; right: 0;
    font-weight: 700; letter-spacing: 5px; margin: 0;
  }
  .front-name { top: 208px; font-size: 36px; color: var(--navy); }
  .back-name { top: 336px; font-size: 38px; color: var(--white); }
  .person { position: absolute; top: 326px; left: 0; right: 0; }
  .person-name { margin: 0; font-size: 25px; font-weight: 700; color: var(--navy); line-height: 30px; }
  .person-title { margin: 0; font-size: 17px; line-height: 22px; }
  .rule { position: absolute; left: 78px; width: 208px; height: 1px; background: var(--rule); }
  .rule-top { top: 387px; }
  .rule-bottom { top: 497px; }
  .contacts { position: absolute; top: 399px; left: 0; right: 0; margin: 0; font-size: 17px; line-height: 21.5px; }
  .contacts b { color: var(--navy); }
  .contacts .web { font-weight: 700; color: var(--navy); }
  .address { position: absolute; top: 509px; left: 0; right: 0; margin: 0; font-size: 17px; line-height: 21.5px; }
  .back-web { position: absolute; top: 524px; left: 0; right: 0; margin: 0; font-size: 19px; letter-spacing: 1.5px; }
</style>
</head>
<body>
<main class="canvas">
  <section class="card card-front">
    <svg class="brand-ring front-ring" width="96" height="96" viewBox="0 0 96 96" aria-hidden="true">
      <circle cx="48" cy="48" r="44" fill="none" stroke="var(--blue-mid)" stroke-width="6"/>
    </svg>
    <h1 class="brand-name front-name">SKYVORNQ</h1>
    <div class="person">
      <p class="person-name">MARCUS DELANE</p>
      <p class="person-title">Managing Director</p>
    </div>
    <div class="rule rule-top"></div>
    <p class="contacts">
      <b>P:</b> 044-570 318 264<br>
      <b>M:</b> 044-570 318 264<br>
      <b>E:</b> hello@skyvornq.com<br>
      <span class="web">www.skyvornq.com</span>
    </p>
    <div class="rule rule-bottom"></div>
    <p class="address">4827 Trellis Hollow Road<br>Fort Pierce, Florida, 34951</p>
  </section>

  <section class="card card-back" role="img" aria-label="Blue gradient card back with brand name">
    <svg class="brand-ring back-ring" width="106" height="106" viewBox="0 0 106 106" aria-hidden="true">
      <circle cx="53" cy="53" r="48" fill="none" stroke="var(--white)" stroke-width="6"/>
    </svg>
    <h2 class="brand-name back-name">SKYVORNQ</h2>
    <p class="back-web">WWW.SKYVORNQ.COM</p>
  </section>
</main>
</body>
</html>
```